Holistic Psychologist needs contemporary business card

I am a psychologist working with adult clients face to face and online. The card needs to work for clients and also referring doctors and medical professionals. It needs to look warm, safe and trustable for clients, but clean and professional enough for doctors. Sometimes I also work in a corporate context.

I am holistic in my approach (mind-body-spirit) so anything conveying connection or integration or wholeness would be good. But again, clean and contemporary please. It can have a little bit of personality.

Probably warm tones and plenty white space to write on one side.

My web pages:
http://mwtherapy.com.au
https://www.facebook.com/HelenaMorrowTherapy?ref=hl
Updates

Hi Designers .. I have decided I do need a new logo before finalising a design for the business cards.  I hope to have this available in 4 days from now.

Kindly,

Helena

New logo now posted, same brief.  Balance of masculine and feminine elements, plenty of white space on one side please.

Keen to see some card designs, thank-you.

Target Market(s)

Audience 1 - Males and females aged 25 years + seeking counselling or coaching. Audience 2 - doctors and health professionals who refer clients.

Industry/Entity Type

Medical

Contact Information for Business Card

Logo

Helena Morrow
Registered Psychologist

M: 0481 552 903
www.mwtherapy.com.au
helena@mwtherapy.com.au
Little blue Facebook icon, with "helena morrow therapy" printed near it.

Font styles to use
Sans Serif

Requirements
Nice to have
• You might want to play with the words "essential you"
Should not have
• Nothing cutesy or too literal

```html
<!DOCTYPE html>
<html lang="en">
<head>
<meta charset="utf-8">
<title>Helena Morrow – Business Card</title>
<link href="https://fonts.googleapis.com/css2?family=Ubuntu:ital,wght@0,400;0,500;1,400&display=swap" rel="stylesheet">
<style>
  :root {
    --page: #ffffff;
    --card-back: #ffffff;
    --card-front: #efefef;
    --card-edge: #8a8a8a;
    --brand-blue: #0b8fd8;
    --text-blue: #0a7cc4;
    --brand-red: #e0262d;
    --social-blue: #3b5998;
    --doodle-light: #f1f1f1;
    --doodle-mid: #d9d9d9;
    --doodle-dark: #c8c8c8;
  }
  * { margin: 0; padding: 0; box-sizing: border-box; }
  html, body {
    width: 1200px; height: 947px; overflow: hidden;
    background: var(--page);
    font-family: "Ubuntu", sans-serif;
  }
  .canvas { position: relative; width: 1200px; height: 947px; }

  .card {
    position: absolute;
    border: 1px solid var(--card-edge);
    overflow: hidden;
  }
  .card--pattern { left: 0; top: 0; width: 580px; height: 937px; background: var(--card-back); }
  .card--details { left: 621px; top: 8px; width: 579px; height: 937px; background: var(--card-front); }

  .doodle-field {
    position: absolute; left: 28px; top: 12px; width: 532px; height: 916px;
    background:
      radial-gradient(circle at 20% 8%,  var(--doodle-dark) 0, transparent 16%),
      radial-gradient(circle at 72% 10%, var(--doodle-dark) 0, transparent 15%),
      radial-gradient(circle at 40% 28%, var(--doodle-mid) 0, transparent 18%),
      radial-gradient(circle at 82% 34%, var(--doodle-dark) 0, transparent 14%),
      radial-gradient(circle at 26% 50%, var(--doodle-mid) 0, transparent 17%),
      radial-gradient(ellipse at 92% 62%, var(--doodle-dark) 0, transparent 22%),
      radial-gradient(circle at 60% 80%, var(--doodle-mid) 0, transparent 18%),
      radial-gradient(circle at 18% 90%, var(--doodle-dark) 0, transparent 15%),
      radial-gradient(circle at 75% 94%, var(--doodle-mid) 0, transparent 14%),
      var(--doodle-light);
  }

  .brand-band {
    position: absolute; left: 0; top: 551px; width: 387px; height: 103px;
    background: var(--brand-blue);
    border-radius: 0 22px 22px 0;
    display: flex; align-items: center; padding-left: 30px;
    z-index: 1;
  }

  .wordmark {
    display: flex; align-items: center;
    color: var(--brand-red); font-weight: 400; white-space: nowrap;
  }
  .wordmark__dot { border-radius: 50%; background: var(--brand-red); flex: none; }
  .brand-band .wordmark { font-size: 33px; gap: 16px; }
  .brand-band .wordmark__dot { width: 52px; height: 52px; }

  .card--details .wordmark {
    position: absolute; left: 98px; top: 87px; font-size: 39px; gap: 22px;
  }
  .card--details .wordmark__dot { width: 64px; height: 64px; }

  .person-name {
    position: absolute; left: 71px; top: 276px;
    font-size: 48px; font-weight: 400; color: var(--text-blue); white-space: nowrap;
  }
  .person-role {
    position: absolute; right: 146px; top: 334px;
    font-size: 22px; font-style: italic; color: var(--brand-red); white-space: nowrap;
  }

  .contact-list { list-style: none; }
  .contact-list li {
    position: absolute; left: 0; width: 579px; text-align: center;
    font-size: 31px; color: var(--text-blue); white-space: nowrap;
  }
  .contact-list .contact-web   { top: 613px; }
  .contact-list .contact-mail  { top: 675px; }
  .contact-list .contact-phone { top: 745px; }
  .contact-list .contact-social {
    top: 815px; display: flex; justify-content: center; align-items: center; gap: 12px;
  }
  .social-square { width: 32px; height: 32px; background: var(--social-blue); flex: none; }
</style>
</head>
<body>
<main class="canvas">
  <section class="card card--pattern">
    <div class="doodle-field" role="img" aria-label="Dense line-drawn doodles of everyday objects covering the card: phone, camera, guitar, laptop, globe, car, clothing, music player and games"></div>
    <div class="brand-band">
      <div class="wordmark"><span class="wordmark__dot"></span><span>Helena Morrow</span></div>
    </div>
  </section>

  <section class="card card--details">
    <div class="wordmark"><span class="wordmark__dot"></span><span>Helena Morrow</span></div>
    <h1 class="person-name">Helena Morrow</h1>
    <p class="person-role">Registered Psychologist</p>
    <ul class="contact-list">
      <li class="contact-web">www.mwtherapy.com.au</li>
      <li class="contact-mail">helena@mwtherapy.com.au</li>
      <li class="contact-phone">M: 0481 552 903</li>
      <li class="contact-social"><span class="social-square"></span><span>“helena morrow therapy”</span></li>
    </ul>
  </section>
</main>
</body>
</html>
```